Willow Fen Racquet Club (Tennis Country Club)

Racquet and Tennis Country Club in Florida.
This web sight is needed for a Privet Tennis club located in Deerfield Beach city in Florida, USA.
We have 10 clay tennis courts and 2 hard tennis courts, small and cozy swimming pool and a clubhouse (see attached pictures) Attached pictures are for information only because we are under a reconstruction.
Updates

I haven't received any source files and web converted files neither!

Target Market(s)

Adult members, Kids members, Tennis players

Coding

Coded - Design and coding required

Number of Pages Required

3 page

Requirements
Must have
• Logo colors (see attached file)

```html
<!DOCTYPE html>
<html lang="en">
<head>
<meta charset="utf-8">
<title>Willow Fen Racquet Club</title>
<link rel="stylesheet" href="https://fonts.googleapis.com/css2?family=Roboto:ital,wght@0,300;0,400;0,500;1,400&display=swap">
<style>
:root{
  --green:#0d5a2c;
  --green-deep:#0a4723;
  --green-bright:#2fbf5b;
  --mint:#e1efe6;
  --dark:#1b1d1c;
  --black:#0b0b0b;
  --text:#333;
  --grey:#e7e7e7;
  --white:#fff;
}
*{box-sizing:border-box;margin:0;padding:0}
html,body{width:1200px;height:3495px;overflow:hidden}
body{font-family:"Roboto",Arial,sans-serif;color:var(--text);background:var(--white);position:relative}
.abs{position:absolute}
.photo{position:absolute}
.btn{position:absolute;display:inline-block;background:var(--green);color:var(--white);font-size:14px;border-radius:16px;padding:9px 18px;text-decoration:none}
h2{position:absolute;font-weight:400;font-size:36px}

/* header */
.hero{position:absolute;left:0;top:0;width:1200px;height:652px;overflow:hidden;
  background:linear-gradient(180deg,#6f97c8 0%,#a9c1dc 38%,#3c4a3a 58%,#7a4b36 80%,#5c3a2c 100%)}
.hero .player{left:760px;top:70px;width:240px;height:582px;background:linear-gradient(180deg,#6a4a3e,#2d3a5c 45%,#1a1a1a 75%);border-radius:90px 90px 10px 10px;opacity:.85}
.nav-bar{position:absolute;left:0;top:0;width:1200px;height:86px;background:rgba(20,28,40,.55)}
.nav{position:absolute;top:28px;left:0;display:flex;font-size:17px;color:var(--white)}
.nav a{color:var(--white);text-decoration:none;position:absolute;white-space:nowrap}
.nav a.active{color:var(--green-bright)}
.brand{position:absolute;left:0;top:0}
.brand-dot{position:absolute;left:129px;top:16px;width:34px;height:34px;border-radius:50%;border:2px solid var(--green)}
.brand-name{position:absolute;left:86px;top:56px;width:120px;text-align:center;font-size:19px;font-weight:500;color:var(--green);white-space:nowrap}
.hero-title{position:absolute;left:90px;top:245px;font-size:66px;font-weight:400;color:var(--white)}
.hero-sub{position:absolute;left:90px;top:335px;font-size:40px;line-height:56px;color:var(--white)}
.watch{position:absolute;left:88px;top:498px;display:flex;align-items:center;color:var(--white);font-size:16px}
.watch i{width:44px;height:44px;border-radius:50%;background:var(--white);margin-right:14px;display:flex;align-items:center;justify-content:center}
.dots{position:absolute;left:1158px;top:315px}
.dots span{display:block;width:8px;height:8px;border-radius:50%;background:rgba(255,255,255,.6);margin-bottom:12px}

/* about */
.about-photo{left:30px;top:690px;width:470px;height:480px;background:radial-gradient(ellipse at 50% 45%,#8fd98f 0%,#c9e9c9 35%,#f4f4f4 70%);}
.about h2{left:520px;top:755px;color:#222}
.ball{position:absolute;left:622px;top:758px;width:38px;height:38px;border-radius:50%;background:radial-gradient(circle at 40% 35%,#eef26a,#c9d02a)}
.about p{position:absolute;left:520px;top:815px;width:575px;font-size:13.5px;line-height:23.5px;color:#444}

/* services */
.services{position:absolute;left:0;top:1170px;width:1200px;height:526px;background:var(--green);overflow:hidden}
.services h2{left:0;width:1200px;text-align:center;top:65px;color:var(--white)}
.svc-frame{position:absolute;border:3px solid var(--white);width:228px;height:217px}
.svc-img{position:absolute;width:228px;height:219px}
.svc-label{position:absolute;width:228px;text-align:center;font-size:16px;color:var(--white)}

/* what we do */
.what h2{left:126px;top:1875px;color:#222}
.what ul{position:absolute;left:126px;top:1932px;list-style:none;font-size:14px;color:#333}
.what li{height:28px;display:flex;align-items:center}
.what li::before{content:"";width:13px;height:13px;border-radius:50%;background:#d0541c;margin-right:10px}
.what-frame{left:634px;top:1830px;width:480px;height:320px;border:2px solid #555}
.what-img{left:613px;top:1848px;width:477px;height:324px;background:linear-gradient(180deg,#cfcfcf,#f2f2f2 45%,#9a9a9a)}
.play{position:absolute;left:814px;top:1974px;width:76px;height:76px;border-radius:50%;background:rgba(40,40,40,.75)}

/* testimonial (children positioned relative to the panel) */
.testi{position:absolute;left:0;top:2337px;width:1200px;height:466px;background:var(--dark);overflow:hidden}
.testi-person{left:47px;top:2272px;width:396px;height:531px;background:linear-gradient(180deg,#f0f0f0,#d7d7d7 55%,#2a2a2a 78%,#c9a58c);border-radius:160px 160px 0 0}
.quote{position:absolute;left:356px;top:52px;font-size:130px;line-height:1;color:var(--green-bright);font-family:Georgia,serif;font-weight:700}
.testi h2{left:457px;top:66px;color:var(--white);font-size:36px}
.testi-text{position:absolute;left:468px;top:128px;width:635px;font-size:13.5px;line-height:29px;color:var(--white)}
.testi-name{position:absolute;left:468px;top:288px;font-size:12.5px;font-style:italic;color:var(--white)}

/* blog */
.blog h2{left:0;width:1200px;text-align:center;top:2903px;color:#222}
.card{position:absolute;top:3003px;width:497px;height:170px;background:var(--white);box-shadow:0 2px 8px rgba(0,0,0,.18)}
.card .thumb{position:absolute;left:0;top:0;width:163px;height:170px;background:linear-gradient(180deg,#dadada,#f5f5f5 40%,#8a8a8a)}
.card .body{position:absolute;left:185px;top:20px;width:290px}
.card h3{font-size:14px;font-weight:400;color:#222}
.card .date{font-size:12px;color:#555;margin-top:8px}
.card p{font-size:12.5px;line-height:18px;color:#555;margin-top:8px;text-align:justify}
.card a{display:block;font-size:12px;color:var(--green);margin-top:6px;text-decoration:none}

/* footer */
.footer{position:absolute;left:0;top:3310px;width:1200px;height:185px;background:var(--black)}
.foot-dot{position:absolute;left:153px;top:3372px;width:34px;height:34px;border-radius:50%;border:2px solid var(--green)}
.foot-brand{position:absolute;left:110px;top:3413px;width:120px;text-align:center;font-size:19px;font-weight:500;color:var(--green);white-space:nowrap}
.social{position:absolute;left:413px;top:3400px;display:flex;gap:8px}
.social span{width:32px;height:32px;border-radius:50%;border:1.5px solid var(--white)}
.foot-links{position:absolute;right:100px;top:3383px;font-size:15px;color:var(--white);display:flex;gap:24px}
.copy{position:absolute;right:100px;top:3427px;font-size:13px;color:var(--white)}
</style>
</head>
<body>

<header class="hero">
  <div class="photo player" role="img" aria-label="Photo of a tennis player standing on a court at sunset"></div>
  <svg class="abs" style="left:0;top:0" width="1200" height="652">
    <polygon points="900,652 1200,420 1200,652" fill="#2fbf5b" opacity=".55"/>
    <polygon points="1000,652 1200,505 1200,652" fill="#e1efe6" opacity=".35"/>
  </svg>
  <div class="nav-bar"></div>
  <svg class="abs" style="left:0;top:0" width="340" height="165"><polygon points="0,0 338,0 160,160" fill="#fff"/></svg>
  <div class="brand"><div class="brand-dot"></div><div class="brand-name">Willow Fen</div></div>
  <nav class="nav">
    <a class="active" style="left:370px">Home</a>
    <a style="left:473px">About us</a>
    <a style="left:600px">Services</a>
    <a style="left:723px">Blog</a>
    <a style="left:820px">Contacts</a>
    <a style="left:970px">
      <svg width="16" height="16" viewBox="0 0 24 24" style="vertical-align:-2px;margin-right:4px"><path fill="#2fbf5b" d="M6.6 10.8a15 15 0 0 0 6.6 6.6l2.2-2.2c.3-.3.7-.4 1-.2 1.1.4 2.3.6 3.6.6.6 0 1 .4 1 1V20c0 .6-.4 1-1 1C10.6 21 3 13.4 3 4c0-.6.4-1 1-1h3.5c.6 0 1 .4 1 1 0 1.3.2 2.5.6 3.6.1.3 0 .7-.2 1z"/></svg>(08) 5550 1420</a>
  </nav>
  <h1 class="hero-title">Tennis Club</h1>
  <div class="hero-sub">Tennis courts, small &amp;<br>Cozy swimming pool</div>
  <div class="watch"><i><svg width="14" height="14" viewBox="0 0 10 10"><polygon points="2,1 9,5 2,9" fill="#0d5a2c"/></svg></i>WATCH VIDEO</div>
  <div class="dots"><span></span><span></span><span></span></div>
</header>

<svg class="abs" style="left:0;top:640px" width="1200" height="70">
  <polygon points="1200,12 1200,62 900,62 960,12" fill="#fff"/>
  <polyline points="960,12 900,62 1200,62" fill="none" stroke="#222" stroke-width="2"/>
</svg>

<section class="about">
  <div class="photo about-photo" role="img" aria-label="Photo of a male tennis player swinging a racquet"></div>
  <h2>About</h2><div class="ball"></div>
  <p>It is a long established fact that a reader will be distracted by the readable content of a page when looking at its layout. The point of using Lorem Ipsum is that it has a more-or-less normal distribution of letters, as opposed to using 'Content here, content here', making it look like readable English. Many desktop publishing packages and web page editors now use Lorem Ipsum as their default model text, the point of using Lorem Ipsum is that it has a more-or-less normal distribution of letters, as opposed to using 'Content here, content here', making it look like readable English. Many desktop publishing packages</p>
  <a class="btn" style="left:520px;top:1005px">Read More</a>
</section>

<section class="services">
  <svg class="abs" style="left:0;top:0" width="1200" height="526">
    <polygon points="1200,0 1200,8 1120,0" fill="#fff"/>
    <polygon points="0,400 0,526 220,526" fill="#0a4723" opacity=".6"/>
    <polygon points="1200,20 1200,526 700,526" fill="#0a4723" opacity=".6"/>
    <polygon points="1200,250 1200,526 890,526 1080,330" fill="#fff"/>
  </svg>
  <h2>Our Services</h2>
  <div class="svc-frame" style="left:121px;top:165px"></div>
  <div class="photo svc-img" style="left:142px;top:184px;background:linear-gradient(180deg,#5b8fd0,#cfe0f2 35%,#2c5c8c 60%,#6b6b6b)" role="img" aria-label="Photo of the club tennis courts"></div>
  <div class="svc-label" style="left:142px;top:418px">Tennis club</div>
  <div class="svc-frame" style="left:466px;top:165px"></div>
  <div class="photo svc-img" style="left:486px;top:184px;background:linear-gradient(180deg,#9aa6a8,#cfd6d6 35%,#1f6fc4 55%,#2a80d8)" role="img" aria-label="Photo of the swimming pool"></div>
  <div class="svc-label" style="left:486px;top:418px">Swimming Pool</div>
  <div class="svc-frame" style="left:777px;top:165px"></div>
  <div class="photo svc-img" style="left:797px;top:184px;background:linear-gradient(180deg,#111,#1d2a20 50%,#2d3b2a)" role="img" aria-label="Photo of the tennis courts at night"></div>
  <div class="svc-label" style="left:797px;top:420px">Tennis Courts</div>
</section>

<section class="what">
  <svg class="abs" style="left:0;top:1696px" width="1200" height="641">
    <polygon points="620,0 1200,0 1200,641" fill="#e1efe6"/>
  </svg>
  <h2>What We do</h2>
  <ul>
    <li>Lorem ipsum dolor sit amet, consectetur adipiscing elit.</li>
    <li>Proin sed sapien sagittis, pellentesque magna quis, venenatis enim.</li>
    <li>Maecenas ut dolor quis quam maximus bibendum.</li>
    <li>Mauris in ipsum et nisl interdum ultrices ut eget turpis.</li>
    <li>Etiam finibus augue nec feugiat suscipit.</li>
    <li>Mauris feugiat magna vel dui commodo efficitur.</li>
  </ul>
  <a class="btn" style="left:126px;top:2122px">Read More</a>
  <div class="abs what-frame"></div>
  <div class="photo what-img" role="img" aria-label="Sketch of the planned clubhouse building"></div>
  <div class="play"><svg width="76" height="76"><polygon points="30,24 54,38 30,52" fill="#fff"/></svg></div>
</section>

<section class="testi">
  <svg class="abs" style="left:0;top:0" width="1200" height="466">
    <polygon points="0,0 200,0 450,466 0,466" fill="#262928"/>
    <line x1="0" y1="30" x2="460" y2="466" stroke="#fff" stroke-width="1.5"/>
  </svg>
  <div class="quote">&ldquo;</div>
  <h2>Testimonial</h2>
  <p class="testi-text">It is a long established fact that a reader will be distracted by the readable content of a page when looking at its layout. The point of using Lorem Ipsum is that it has a more-or-less normal distribution of letters, as opposed to using 'Content here, content here', making it look like readable English. Many desktop publishing packages and web page editors now use Lorem Ipsum as their default model text, and a search for 'lorem ipsum' will uncover many web sites still in their infancy.</p>
  <div class="testi-name">- &nbsp;Helen Marsh, CFO, Northgate Capital Partners</div>
  <svg class="abs" style="left:475px;top:345px" width="62" height="16">
    <path d="M2 8h24M2 8l6-5M2 8l6 5" stroke="#fff" stroke-width="2.5" fill="none"/>
    <path d="M34 8h24M58 8l-6-5M58 8l-6 5" stroke="#fff" stroke-width="2.5" fill="none"/>
  </svg>
</section>
<div class="photo testi-person" role="img" aria-label="Photo of a female tennis player holding a racquet and ball"></div>

<section class="blog">
  <svg class="abs" style="left:0;top:2803px" width="1200" height="507">
    <polygon points="800,0 1200,0 1200,470" fill="#e1efe6"/>
    <polygon points="0,310 0,507 215,507" fill="#e7e7e7"/>
  </svg>
  <h2>Latest Blog</h2>
  <article class="card" style="left:88px">
    <div class="thumb" role="img" aria-label="Sketch of a clubhouse exterior"></div>
    <div class="body"><h3>Nemo Enim Ipsam Volup</h3><div class="date">09-07-2017</div>
    <p>Lorem Ipsum has been the industry's standard dummy text ever since the 1500s, when an unknown printer took a galley</p><a>Read More &gt;&gt;</a></div>
  </article>
  <article class="card" style="left:613px">
    <div class="thumb" role="img" aria-label="Sketch of a clubhouse terrace"></div>
    <div class="body"><h3>Nemo Enim Ipsam Volup</h3><div class="date">09-07-2017</div>
    <p>Lorem Ipsum has been the industry's standard dummy text ever since the 1500s, when an unknown printer took a galley</p><a>Read More &gt;&gt;</a></div>
  </article>
</section>

<footer class="footer">
  <svg class="abs" style="left:0;top:0" width="480" height="185">
    <polygon points="0,0 215,0 400,185 0,185" fill="#e7e7e7"/>
    <line x1="215" y1="0" x2="400" y2="185" stroke="#fff" stroke-width="3"/>
  </svg>
</footer>
<div class="foot-dot"></div>
<div class="foot-brand">Willow Fen</div>
<div class="social"><span></span><span></span><span></span><span></span><span></span></div>
<div class="foot-links"><span>About us</span><span>Services</span><span>Blog</span><span>Contacts</span></div>
<div class="copy">Copyright © 2018 All Rights Reserved</div>

</body>
</html>
```